Packaging design for a reclosable bag for our product

We have a logo, and we need to put it on packaging for our product and while we want the look to be simple, we want it to follow good design principles and also contain spaces for other product descriptions.

There will be 5 sizes at launch so I'd like 5 variations, one for each size.

I've included a few mockups of the type of bag that I made but they are all just rough ideas that I had.

I want the brand to look scientific and methodical and even a bit quirky, as in "wow this is a serious product but also a bit unusual."

```html
<!DOCTYPE html>
<html lang="en">
<head>
<meta charset="utf-8">
<title>KR2 Bias Lighting – Extra Large Pouch</title>
<link href="https://fonts.googleapis.com/css2?family=Michroma&family=Poppins:wght@300;400;600&display=swap" rel="stylesheet">
<style>
  :root {
    --backdrop: #d6d6d6;
    --pouch-upper: #3b3b3b;
    --pouch-lower: #161616;
    --pouch-edge: #2a2a2a;
    --zip-line: #555555;
    --band-white: #f4f4f4;
    --band-shade: #bdbdbd;
    --band-rule: #0c0c0c;
    --ink-light: #f2f2f2;
    --ink-soft: #cfcfcf;
    --ink-dark: #1b1b1b;
  }
  * { box-sizing: border-box; margin: 0; padding: 0; }
  html, body {
    width: 1200px;
    height: 760px;
    overflow: hidden;
    background: var(--backdrop);
  }
  .pouch {
    position: absolute;
    left: 356px;
    top: 60px;
    width: 488px;
    height: 640px;
    background: linear-gradient(to bottom, var(--pouch-upper) 0%, #333 56%, var(--pouch-lower) 56%, var(--pouch-lower) 100%);
    overflow: hidden;
  }
  .pouch-seal {
    position: absolute;
    inset: 10px 14px 14px 14px;
    border: 1px solid rgba(255,255,255,0.06);
    border-radius: 14px;
  }
  .zip-track {
    position: absolute;
    left: 44px;
    right: 56px;
    top: 72px;
    height: 6px;
    border-top: 1px solid var(--zip-line);
    border-bottom: 1px solid #262626;
    border-radius: 3px;
  }
  .brand-name {
    position: absolute;
    left: 0;
    right: 0;
    top: 104px;
    text-align: center;
    font-family: "Poppins", sans-serif;
    font-weight: 600;
    font-size: 196px;
    line-height: 1;
    letter-spacing: -8px;
    color: var(--ink-light);
  }
  .category-band {
    position: absolute;
    left: 0;
    right: 0;
    top: 301px;
    height: 54px;
    background: var(--band-rule);
  }
  .category-band-fill {
    position: absolute;
    left: 0;
    right: 0;
    top: 9px;
    height: 36px;
    background: linear-gradient(to right, var(--band-shade) 0%, var(--band-white) 10%, var(--band-white) 90%, var(--band-shade) 100%);
    display: flex;
    align-items: center;
    justify-content: center;
  }
  .category-label {
    font-family: "Michroma", sans-serif;
    font-size: 22px;
    letter-spacing: 1px;
    color: var(--ink-dark);
  }
  .size-name {
    position: absolute;
    left: 0; right: 0;
    top: 392px;
    text-align: center;
    font-family: "Poppins", sans-serif;
    font-weight: 300;
    font-size: 17px;
    letter-spacing: 0.5px;
    color: var(--ink-soft);
  }
  .size-length {
    position: absolute;
    left: 0; right: 0;
    top: 412px;
    text-align: center;
    font-family: "Poppins", sans-serif;
    font-weight: 300;
    font-size: 90px;
    line-height: 1.1;
    color: var(--ink-light);
  }
  .spec-list {
    position: absolute;
    left: 0; right: 0;
    top: 518px;
    text-align: center;
    font-family: "Poppins", sans-serif;
    font-weight: 400;
    font-size: 18px;
    line-height: 30px;
    color: var(--ink-soft);
  }
</style>
</head>
<body>
  <div class="pouch">
    <div class="pouch-seal"></div>
    <div class="zip-track"></div>
    <div class="brand-name">KR2</div>
    <div class="category-band">
      <div class="category-band-fill">
        <span class="category-label">BIAS LIGHTING</span>
      </div>
    </div>
    <div class="size-name">EXTRA LARGE</div>
    <div class="size-length">5m</div>
    <div class="spec-list">
      <p>6500K White Bias Lighting</p>
      <p>Simulated D65 CRI 90+</p>
    </div>
  </div>
</body>
</html>
```